Vibrant, yet professional, stationery set and other designs required.

I need to source a fantastic designer for a new project as part of my company using a new logo designed via sketch harbor.

**UPDATE** I am not looking for just 'fine' design that will suffice. I am looking for something great.

We are a life assurance brokerage based in Dublin, Ireland and BrightRoost.ie is our new website aimed at providing services for young families in Ireland. We are hoping to be the 'Velro' level of service providers in this area and I am looking for the quality of design to reflect this :-) Hopefully that makes sense!

I have a preference for straight lines over curves and waves.

I need...

1. Business card
2. Letterhead
3. Banner (for printing - 76cm X 305cm)
4. Car branding for KORVA 9 (2014 sport model) I believe the templates are freely available online.

Target Market(s)

Parents in Ireland - Aged 27 to 50.

Industry/Entity Type

Financial Planning

Colors

Designer to choose colors to be used in the design.

Requirements
Must have
• All of the items listed in the description above. I like clean, bright, legible, vibrant and professional design.
Should not have
• No silly or 'cheap' looking designs. This is a professional company looking to provide a professional service.

```html
<!DOCTYPE html>
<html lang="en">
<head>
<meta charset="utf-8">
<title>BrightRoost.ie – Business Card</title>
<link href="https://fonts.googleapis.com/css2?family=Source+Sans+3:wght@400;600&display=swap" rel="stylesheet">
<style>
  :root {
    --backdrop: #e9e6e1;
    --card-white: #fbfbfb;
    --slate: #7a9097;
    --slate-text: #66777d;
    --ink: #4a4f52;
    --sky: #35c0e6;
    --lime: #86c21a;
    --orange: #ff6a00;
  }
  * { margin: 0; padding: 0; box-sizing: border-box; }
  html, body { width: 1200px; height: 800px; overflow: hidden; }
  body {
    background: var(--backdrop);
    font-family: "Source Sans 3", sans-serif;
    display: flex;
    align-items: center;
    justify-content: center;
    gap: 60px;
  }
  .card {
    width: 525px;
    height: 300px;
    position: relative;
    box-shadow: 0 6px 18px rgba(0,0,0,0.12);
  }
  .card--front { background: var(--card-white); }
  .card--back {
    background: var(--slate);
    display: flex;
    align-items: center;
    justify-content: center;
    gap: 16px;
  }

  .wordmark {
    position: absolute;
    left: 40px;
    top: 124px;
    font-size: 40px;
    font-weight: 600;
    color: var(--slate-text);
    letter-spacing: -0.5px;
  }
  .wordmark-dot {
    position: absolute;
    left: 40px;
    top: 104px;
    width: 14px;
    height: 14px;
    border-radius: 50%;
    background: var(--orange);
  }

  .contact {
    position: absolute;
    right: 34px;
    top: 36px;
    text-align: right;
    color: var(--ink);
    font-size: 14px;
    line-height: 1.35;
  }
  .contact-name {
    color: var(--sky);
    font-weight: 600;
    font-size: 18px;
    letter-spacing: 0.3px;
  }
  .contact-role {
    color: var(--lime);
    font-weight: 600;
    font-size: 15px;
    margin-bottom: 4px;
  }
  .contact-line {
    display: flex;
    justify-content: flex-end;
    align-items: center;
    gap: 8px;
  }
  .contact-line svg { width: 12px; height: 12px; flex: none; }
  .contact-address { padding-right: 20px; }

  .back-mark {
    font-size: 44px;
    font-weight: 600;
    color: var(--card-white);
    letter-spacing: -0.5px;
  }
  .back-dot {
    width: 22px;
    height: 22px;
    border-radius: 50%;
    background: var(--lime);
  }
</style>
</head>
<body>
  <section class="card card--front">
    <span class="wordmark-dot"></span>
    <div class="wordmark">BrightRoost.ie</div>

    <div class="contact">
      <div class="contact-name">AIDAN CARROLL</div>
      <div class="contact-role">CEO/FOUNDER</div>
      <div class="contact-address">14 Larkfield Row</div>
      <div class="contact-address">Dublin 6, D06 K2X4</div>
      <div class="contact-line">01 555 0142
        <svg viewBox="0 0 12 12" aria-hidden="true"><path d="M1 4 Q6 0 11 4 L9.5 5.5 L8 4.5 L4 4.5 L2.5 5.5 Z M3 6 H9 L10 11 H2 Z" fill="var(--sky)"/></svg>
      </div>
      <div class="contact-line">087 555 0193
        <svg viewBox="0 0 12 12" aria-hidden="true"><rect x="3" y="0.5" width="6" height="11" rx="1" fill="none" stroke="var(--sky)" stroke-width="1.3"/></svg>
      </div>
      <div class="contact-line">01 555 0177
        <svg viewBox="0 0 12 12" aria-hidden="true"><rect x="3" y="1" width="6" height="4" fill="var(--sky)"/><rect x="1" y="5" width="10" height="5" rx="1" fill="var(--sky)"/></svg>
      </div>
      <div class="contact-line">hello@brightroost.ie
        <svg viewBox="0 0 12 12" aria-hidden="true"><rect x="0.5" y="2.5" width="11" height="7" fill="var(--sky)"/><path d="M0.5 2.5 L6 7 L11.5 2.5" fill="none" stroke="#fff" stroke-width="1"/></svg>
      </div>
      <div class="contact-line">www.brightroost.ie
        <svg viewBox="0 0 12 12" aria-hidden="true"><circle cx="6" cy="6" r="5.5" fill="var(--sky)"/><path d="M0.5 6 H11.5 M6 0.5 Q2.5 6 6 11.5 M6 0.5 Q9.5 6 6 11.5" fill="none" stroke="#fff" stroke-width="0.8"/></svg>
      </div>
    </div>
  </section>

  <section class="card card--back">
    <span class="back-dot"></span>
    <div class="back-mark">BrightRoost.ie</div>
  </section>
</body>
</html>
```